Vietnam Motorcycle Trip TRAVEL GUIDE!! Book Cover!

I need an adventurous book cover for a book called "THROTTLE MERIDIAN: A Wanderer's Manual for Crossing the Breadth of Vietnam". I would like people to look at the cover and think adventure and Vietnam. I want it to appeal to backpackers and people who have not travelled to Vietnam. A motorbike riding along a road in Vietnam would be ideal with some landscapes to suggest we are definitely in Vietnam. The rear cover could perhaps be one of Vietnam's tropical beaches or something else that says "this place is a paradise". It could also be something else that is quinessentially Vietnamese.

The book will be A5 Dimensions. And it will also need a printable A5 interior cover too. The interior covers can just be images. No text needed. These interior images can be motorcycle related or Vietnam related. Perhaps some images of Vietnam or some Pho or Banh Mi to give it a bit of flavour. Or a long open road with a motorbike on it.

Please leave space in the external rear, lower right hand corner for a barcode.

I've attached some images to gain inspiration from. And a sample chapter.

Colours I'd like to see on there - greens, camoflague perhaps, yellow, brown, blue.

Target Market(s)

Male backpackers aged 18-35 years old. New Zealand and Australian travellers.

Font styles to use
Serif
Sans Serif

Requirements
Must have
• Exterior and Interior covers.
Barcode space.
Title and subtitle.
Synopsis on rear cover.
Exciting title fonts - perhaps Brushstroke or something equally exciting and rugged
Nice to have
• Colours I'd like to see on there - greens, camoflague perhaps, yellow, brown, blue.

A motorbike riding on the open road of Vietnam.

Rice paddies, beaches, Korvan Conflict stuff perhaps.

A New Zealand Flag
A Vietnam Flag
Should not have
• Scenery from countries outside Southeast Asia

```html
<!DOCTYPE html>
<html lang="en">
<head>
<meta charset="utf-8">
<title>Throttle Meridian – Cover Spread</title>
<link rel="stylesheet" href="https://fonts.googleapis.com/css2?family=Anton&family=Permanent+Marker&family=Oswald:wght@500;600&family=Open+Sans:wght@400;600;700&display=swap">
<style>
  :root {
    --page-bg: #d6d6d6;
    --cover-yellow: #f6d21a;
    --title-blue: #1e73c8;
    --ink: #141414;
    --spine-black: #111111;
    --photo-green: #5d7a3c;
    --photo-haze: #b9c48a;
    --photo-sky: #e9d98a;
    --dusk-brown: #6b4a1e;
  }
  * { box-sizing: border-box; margin: 0; padding: 0; }
  html, body { width: 896px; height: 1200px; overflow: hidden; }
  body {
    background: var(--page-bg);
    font-family: "Open Sans", Arial, sans-serif;
    color: var(--ink);
    position: relative;
  }
  .spread {
    position: absolute;
    left: 18px; top: 330px;
    width: 860px; height: 540px;
    display: flex;
    box-shadow: 0 6px 18px rgba(0,0,0,.25);
  }
  .back-cover, .front-cover {
    width: 410px; height: 100%;
    background: var(--cover-yellow);
    position: relative;
    overflow: hidden;
  }
  .spine {
    width: 40px; height: 100%;
    background: var(--spine-black);
    position: relative;
  }
  /* back */
  .back-headline {
    position: absolute; left: 22px; top: 22px; width: 366px;
    font-family: "Anton", Impact, sans-serif;
    font-size: 22px; line-height: 1.12;
    color: var(--title-blue); text-transform: uppercase;
  }
  .back-headline span { color: var(--ink); }
  .synopsis {
    position: absolute; left: 22px; top: 84px; width: 366px;
    font-size: 9px; line-height: 1.45;
  }
  .synopsis ul { margin: 6px 0 6px 12px; }
  .synopsis li { margin-bottom: 1px; }
  .paradise {
    position: absolute; left: 22px; top: 232px;
    font-family: "Permanent Marker", cursive;
    font-size: 30px; color: var(--title-blue);
    text-transform: uppercase;
  }
  .author-bio {
    position: absolute; left: 22px; top: 282px; width: 366px;
    font-size: 9px; line-height: 1.45;
  }
  .author-bio strong { color: var(--title-blue); }
  .back-photo {
    position: absolute; left: 0; bottom: 0; width: 410px; height: 190px;
    background: linear-gradient(180deg, var(--cover-yellow) 0%, #d9a722 45%, var(--dusk-brown) 100%);
  }
  .barcode-space {
    position: absolute; right: 20px; bottom: 20px; width: 110px; height: 66px;
    background: #ffffff;
  }
  /* spine */
  .spine-title {
    position: absolute; left: 50%; top: 24px;
    transform: translateX(-50%);
    writing-mode: vertical-rl;
    font-family: "Anton", Impact, sans-serif;
    font-size: 20px; letter-spacing: 1px;
    color: var(--cover-yellow);
  }
  .spine-author {
    position: absolute; left: 50%; bottom: 22px;
    transform: translateX(-50%);
    writing-mode: vertical-rl;
    font-family: "Oswald", Arial, sans-serif; font-weight: 500;
    font-size: 11px; letter-spacing: 1px; color: #ffffff;
  }
  /* front */
  .front-title {
    position: absolute; left: 0; top: 22px; width: 100%;
    text-align: center;
  }
  .title-main {
    display: block;
    font-family: "Anton", Impact, sans-serif;
    font-size: 50px; line-height: 1; color: var(--title-blue);
    letter-spacing: 1px;
  }
  .title-second {
    display: block; margin-top: 4px;
    font-family: "Permanent Marker", cursive;
    font-size: 46px; line-height: 1; color: var(--ink);
  }
  .subtitle-band {
    position: absolute; left: 34px; top: 150px; width: 342px;
    background: var(--ink); color: var(--cover-yellow);
    font-family: "Oswald", Arial, sans-serif; font-weight: 600;
    font-size: 13px; line-height: 1.3; letter-spacing: .5px;
    text-align: center; text-transform: uppercase;
    padding: 6px 10px;
  }
  .front-photo {
    position: absolute; left: 0; top: 215px; width: 410px; height: 265px;
    background: linear-gradient(180deg, var(--photo-sky) 0%, var(--photo-haze) 30%, var(--photo-green) 75%, #3f5a2a 100%);
  }
  .front-author {
    position: absolute; left: 0; bottom: 18px; width: 100%;
    text-align: center;
    font-family: "Oswald", Arial, sans-serif; font-weight: 600;
    font-size: 24px; letter-spacing: 1px; color: var(--ink);
  }
</style>
</head>
<body>
  <main class="spread">
    <section class="back-cover">
      <h2 class="back-headline">Travel like a pro <span>in a country where bribing cops is normal!</span></h2>
      <div class="synopsis">
        <p>Every year thousands of backpackers arrive in Vietnam hungry for adventure, and most leave having seen only a fraction of it. This guide shows you how to buy a bike, plan a route from north to south, and handle the roads, the weather and the police like a seasoned rider.</p>
        <ul>
          <li>Buy and sell a bike without getting ripped off</li>
          <li>Pick the best passes, coasts and mountain loops</li>
          <li>Deal with checkpoints calmly and keep your cash</li>
          <li>Find cheap food, beds and mechanics on the road</li>
        </ul>
        <p>Grab your helmet and let's get going.</p>
      </div>
      <p class="paradise">This place is a paradise</p>
      <p class="author-bio"><strong>CALLUM HARTWELL</strong> has spent years riding every corner of Vietnam on a battered scooter, living on pho and coffee. He wrote this book so your first trip is safer, cheaper and far more fun.</p>
      <div class="back-photo" role="img" aria-label="Silhouette of a rider on a motorbike against a golden sunset over Vietnamese hills"></div>
      <div class="barcode-space" aria-hidden="true"></div>
    </section>

    <section class="spine">
      <span class="spine-title">THROTTLE MERIDIAN</span>
      <span class="spine-author">CALLUM HARTWELL</span>
    </section>

    <section class="front-cover">
      <h1 class="front-title">
        <span class="title-main">THROTTLE</span>
        <span class="title-second">MERIDIAN</span>
      </h1>
      <p class="subtitle-band">A Wanderer's Manual for Crossing<br>the Breadth of Vietnam</p>
      <div class="front-photo" role="img" aria-label="Rider standing with arms raised beside a motorbike on a mountain road overlooking green Vietnamese valleys"></div>
      <p class="front-author">CALLUM HARTWELL</p>
    </section>
  </main>
</body>
</html>
```